Signage Design Project

We need a logo and signage for the shopfront of a personal fitness training gym and coaching facility. We want the signage to cover the glass shopfront windows which consist of 4 glass windows with dimensions: 1 of 200cm x 180cm, 2 of 180cm x 135cm and 1 of 180cm x 180cm. The windows that are 200x 180 and 180x180 are the most visable/ important. We want the 200x180 to display the logo and our name which is "Ridgeline Fitness Centre" with further information of: Your personal training studio and boutique coaching gym Ph: 9471 2836.
For the window with 180 x 180cm measurement we want to list the services we provide which are:
Personal Training Sessions | Group Classes|Weight Loss |Toning & Sculpting|Bodybuilding I Cardio|Weights| Kettlebells| Boxing| Circuits I Team Building Programs| Boot Camp I Healthy Lifestyle & Wellness Coaching
The 2 windows 180x135cm are diagonal to the entry of the shop. We want them to be the same and plainer in design with the words: Ridgeline Fitness Centre
Personal Training Studio and Boutique Coaching Gym
The signage design also includes an acrylic window box that lights up which is to display the logo and Ridgeline Fitness Centre

```html
<!DOCTYPE html>
<html lang="en">
<head>
<meta charset="utf-8">
<title>Ridgeline Fitness Centre – Shopfront Signage</title>
<link href="https://fonts.googleapis.com/css2?family=Varela+Round&family=Roboto:wght@700&display=swap" rel="stylesheet">
<style>
  :root{
    --canvas:#0a7896;
    --blue-light:#21aee0;
    --blue-dark:#0a6796;
    --green:#9cbc2b;
    --white:#ffffff;
    --ink-blue:#1d9fd2;
  }
  *{box-sizing:border-box;margin:0;padding:0}
  html,body{width:1200px;height:900px;overflow:hidden;background:var(--canvas)}
  .canvas{position:relative;width:1200px;height:900px}

  /* main window sign */
  .main-sign{position:absolute;left:205px;top:100px;width:365px;height:310px;background:var(--white);padding:18px 28px}
  .main-sign__panel{position:relative;width:100%;height:100%;overflow:hidden;
    background:radial-gradient(ellipse at 45% 35%,var(--blue-light),var(--blue-dark) 85%);
    font-family:"Varela Round",sans-serif;color:var(--white);text-align:center}
  .main-sign__curves{position:absolute;inset:0;width:100%;height:100%}
  .main-sign__content{position:relative;padding-top:20px}
  .brand-dot{display:block;width:34px;height:34px;border-radius:50%;background:var(--white);margin:0 auto 10px}
  .brand-name{font-size:40px;letter-spacing:2px;line-height:1}
  .brand-sub{display:inline-block;margin-top:10px;border:2px dashed var(--white);border-radius:12px;padding:3px 12px;font-size:20px}
  .tagline{margin-top:16px;font-size:14.5px;line-height:1.1;letter-spacing:1px}
  .phone{display:flex;align-items:center;justify-content:center;gap:8px;margin-top:14px;font-size:22px;letter-spacing:1px}

  /* services window */
  .services-sign{position:absolute;left:585px;top:510px;width:210px;height:250px;background:var(--white);overflow:hidden;text-align:center}
  .services-sign__curves{position:absolute;left:0;bottom:0;width:100%;height:110px}
  .services-sign .brand-dot{width:14px;height:14px;margin:14px auto 3px;background:var(--ink-blue)}
  .services-sign .brand-name{font-family:"Varela Round",sans-serif;font-size:16px;color:var(--ink-blue);letter-spacing:1px}
  .services-list{margin-top:22px;font-family:"Roboto",sans-serif;font-weight:700;font-size:7.6px;line-height:16.5px;color:var(--ink-blue)}
  .services-list .sep{color:var(--green)}
  .athlete-photo{position:absolute;right:18px;bottom:8px;width:95px;height:80px;border-radius:6px;
    background:linear-gradient(160deg,#f4d9c4,#4aa9d6 60%,#2f6f8f)}

  /* narrow entry window */
  .entry-sign{position:absolute;left:830px;top:540px;width:78px;height:220px;background:var(--white);overflow:hidden;text-align:center;font-family:"Varela Round",sans-serif}
  .entry-sign__curves{position:absolute;left:0;bottom:0;width:100%;height:90px}
  .entry-sign .brand-dot{width:9px;height:9px;margin:40px auto 3px;background:var(--ink-blue)}
  .entry-sign .brand-name{font-size:9px;color:var(--ink-blue)}
  .entry-sign .brand-sub{font-size:7px;color:var(--ink-blue);border:1px dashed var(--ink-blue);border-radius:5px;padding:1px 4px;margin-top:3px}
  .entry-sign__tag{margin-top:5px;font-size:5.5px;line-height:1.2;color:var(--green)}
  .entry-sign__tag span{color:var(--ink-blue)}
  .entry-photo{position:absolute;left:16px;bottom:22px;width:44px;height:62px;border-radius:4px;
    background:linear-gradient(160deg,#f4d9c4,#4aa9d6 60%,#2f6f8f)}
</style>
</head>
<body>
<main class="canvas">

  <section class="main-sign">
    <div class="main-sign__panel">
      <svg class="main-sign__curves" viewBox="0 0 309 274" preserveAspectRatio="none" aria-hidden="true">
        <path d="M0 0 H95 C40 15 12 50 0 95 Z" fill="var(--green)"/>
        <path d="M309 170 V274 H215 C270 250 300 215 309 170 Z" fill="var(--green)"/>
      </svg>
      <div class="main-sign__content">
        <span class="brand-dot"></span>
        <h1 class="brand-name">RIDGELINE</h1>
        <p class="brand-sub">Fitness Centre</p>
        <p class="tagline">Your personal training<br>studio &amp; boutique<br>coaching gym</p>
        <p class="phone">
          <svg width="12" height="20" viewBox="0 0 12 20" aria-hidden="true"><rect x="1" y="1" width="10" height="18" rx="2" fill="var(--white)"/><rect x="3" y="4" width="6" height="6" fill="var(--blue-dark)"/></svg>
          9471-2836
        </p>
      </div>
    </div>
  </section>

  <section class="services-sign">
    <svg class="services-sign__curves" viewBox="0 0 210 110" preserveAspectRatio="none" aria-hidden="true">
      <path d="M0 0 C30 60 110 90 210 70 V110 H0 Z" fill="var(--green)"/>
      <path d="M0 40 C50 85 130 100 210 85 V110 H0 Z" fill="var(--white)"/>
      <path d="M60 110 C120 100 180 80 210 40 V110 Z" fill="var(--blue-dark)"/>
    </svg>
    <span class="brand-dot"></span>
    <h2 class="brand-name">RIDGELINE</h2>
    <p class="services-list">
      Personal Training Sessions <span class="sep">|</span> Group Classes<br>
      Weight Loss <span class="sep">|</span> Toning &amp; Sculpting <span class="sep">|</span> BodyBuilding<br>
      Cardio <span class="sep">|</span> Weights <span class="sep">|</span> Kettlebells Boxing <span class="sep">|</span> Circuits<br>
      TeamBuildingPrograms <span class="sep">|</span> BootCamp<br>
      HealthyLifestyle &amp; Wellness Coaching
    </p>
    <div class="athlete-photo" role="img" aria-label="Photo of a woman in activewear stretching on the floor"></div>
  </section>

  <section class="entry-sign">
    <svg class="entry-sign__curves" viewBox="0 0 78 90" preserveAspectRatio="none" aria-hidden="true">
      <path d="M0 10 C20 60 50 75 78 70 V90 H0 Z" fill="var(--green)"/>
      <path d="M30 90 C55 80 72 50 78 10 V90 Z" fill="var(--blue-dark)"/>
    </svg>
    <span class="brand-dot"></span>
    <h2 class="brand-name">RIDGELINE</h2>
    <p class="brand-sub">Fitness Centre</p>
    <p class="entry-sign__tag">Personal Training<br><span>Studio &amp; Boutique Coaching Gym</span></p>
    <div class="entry-photo" role="img" aria-label="Photo of a woman in activewear stretching"></div>
  </section>

</main>
</body>
</html>
```